Shopify Web-Page "Tiny-ThreadDays

We are building a new business in Switzerland offering premium sewing holiday camps for kids aged 9–14. In enclosed brief outlines our requirements for a complete Shopify homepage design and a multilingual logo creation.
Domains: tiny-threaddays.ch ; tiny-giornifilo.ch ; tiny-fadentage.ch

Project Overview
We are looking for:
1. A modern, fully designed Shopify homepage in English using standard Shopify content blocks (no custom coding), which we can later update ourselves. Supporting Multilanguage (EN, German, Italian).

2. A logo design that includes the brand identity and communicates our multilingual, creative, and child-focused positioning.

All details in enclosed

```html
<!DOCTYPE html>
<html lang="en">
<head>
<meta charset="utf-8">
<title>Tiny-ThreadDays – Sewing Holiday Camps for Kids</title>
<link href="https://fonts.googleapis.com/css2?family=Outfit:wght@400;500;600;700&display=swap" rel="stylesheet">
<style>
:root{
  --coral:#e0684f;
  --teal:#245f68;
  --ink:#1f2328;
  --muted:#6b6f74;
  --line:#dcdde3;
  --footer:#121212;
  --white:#ffffff;
}
*{box-sizing:border-box;margin:0;padding:0}
html,body{width:1200px;height:3895px;overflow:hidden}
body{font-family:"Outfit",sans-serif;color:var(--ink);background:var(--white);position:relative}
.wrap{width:978px;margin:0 auto;position:relative}
.btn{display:inline-block;background:var(--coral);color:var(--white);font-size:13px;font-weight:500;letter-spacing:.6px;text-transform:uppercase;padding:12px 28px;border-radius:3px}

/* header */
.site-header{height:94px;display:flex;align-items:center}
.site-header .wrap{display:flex;align-items:center;justify-content:space-between}
.brand{display:flex;align-items:center;gap:8px;font-size:22px;font-weight:700;color:var(--coral)}
.brand-dot{width:14px;height:14px;border-radius:50%;background:var(--teal)}
.main-nav{display:flex;gap:38px;font-size:13px;font-weight:500;margin-left:60px}
.main-nav .active{color:var(--coral)}
.header-tools{display:flex;align-items:center;gap:36px;font-size:13px;font-weight:500}

/* hero */
.hero{height:607px;background:linear-gradient(135deg,#6b5148,#4a3c38 45%,#7a5a4c);display:flex;flex-direction:column;align-items:center;justify-content:center;text-align:center;color:var(--white)}
.hero h1{font-size:38px;font-weight:500;line-height:44px;text-transform:uppercase}
.hero h1 span{display:block;color:var(--coral);font-weight:700}
.hero p{font-size:20px;line-height:30px;margin:12px 0 22px}

/* mentors */
.mentors{margin-top:97px;height:367px;border-radius:6px;background:linear-gradient(180deg,#b5a08b 0%,#6f5b4c 55%,#1e1a18 100%);padding:0 48px;display:flex;flex-direction:column;justify-content:flex-end;padding-bottom:26px;color:var(--white)}
.mentors h2{font-size:27px;font-weight:500;line-height:35px;text-transform:uppercase}
.mentors p{font-size:16px;line-height:22px;margin:14px 0 16px;max-width:560px}
.mentors .btn{align-self:flex-start}

/* section head */
.section-head{border-top:2px solid var(--line);position:relative;padding-top:22px}
.section-head::before{content:"";position:absolute;left:0;top:-2px;width:55px;height:4px;background:var(--coral)}
.section-head h2{font-size:30px;font-weight:500;padding-left:2px}

/* how it works */
.how{margin-top:100px}
.steps{display:flex;gap:14px;margin-top:28px}
.step{width:234px;height:326px;background:var(--white);box-shadow:0 4px 12px rgba(0,0,0,.12);border-radius:4px;overflow:hidden}
.step .ph{height:250px}
.step h3{font-size:23px;font-weight:500;text-align:center;line-height:76px}

/* features */
.features{margin-top:80px;height:297px;background:var(--teal);color:var(--white);padding-top:68px}
.features .section-head{border-color:rgba(255,255,255,.3)}
.features .section-head::before{background:var(--white)}
.features .section-head h2{font-size:30px}
.feature-list{display:flex;gap:0;margin-top:26px}
.feature{font-size:12px;line-height:15px}
.feature strong{display:block;font-size:16px;font-weight:600;margin-bottom:4px}

/* camps */
.camps{margin-top:99px}
.camp-list{display:flex;gap:20px;margin-top:28px}
.camp{width:313px;height:459px;box-shadow:0 4px 12px rgba(0,0,0,.12);border-radius:4px;overflow:hidden;text-align:center}
.camp .ph{height:335px}
.camp h3{font-size:27px;font-weight:500;margin-top:18px}
.camp p{font-size:15px;line-height:21px;color:var(--muted);margin:10px auto 0;width:300px}
.center{text-align:center}
.camps .center{margin-top:35px}

/* faq */
.faq{margin-top:96px}
.faq-list{margin-top:14px}
.faq-item{border-bottom:1px solid var(--line);padding:14px 0 14px 0;position:relative}
.faq-item h3{font-size:20px;font-weight:500;display:flex;align-items:center;gap:8px}
.faq-item p{font-size:13px;color:var(--muted);margin:6px 0 0 24px}
.faq-item .toggle{position:absolute;right:200px;top:14px}
.faq-item:last-child{border-bottom:none}
.faq .center{margin-top:24px}

/* newsletter band */
.loop{position:absolute;top:3404px;left:0;width:1200px;height:157px;background:var(--coral);color:var(--white)}
.loop .wrap{display:flex;justify-content:space-between;align-items:center;height:100%}
.loop h2{font-size:30px;font-weight:600}
.loop p{font-size:15px;line-height:21px;margin-top:12px}
.loop .btn{background:var(--teal);padding:12px 30px}

/* footer */
.site-footer{position:absolute;top:3561px;left:0;width:1200px;height:334px;background:var(--footer);color:var(--white)}
.footer-cols{display:flex;padding-top:50px;height:272px}
.footer-brand{width:338px;display:flex;flex-direction:column;align-items:center;padding-top:18px}
.footer-brand .brand{font-size:34px}
.footer-brand small{font-size:11px;letter-spacing:1px;margin-top:6px}
.footer-col{width:186px}
.footer-col h4{font-size:16px;font-weight:600;margin-bottom:10px}
.footer-col li{list-style:none;font-size:11px;line-height:22px;text-transform:uppercase;padding-left:2px}
.footer-news{width:268px}
.footer-news p{font-size:12px;line-height:18px;text-transform:uppercase}
.signup{display:flex;margin-top:16px}
.signup span{width:165px;height:42px;background:var(--white);color:#555;font-size:11px;padding:14px 12px;border-radius:3px 0 0 3px}
.signup b{width:92px;height:42px;background:var(--teal);font-size:11px;font-weight:600;display:flex;align-items:center;justify-content:center;border-radius:0 3px 3px 0}
.footer-bottom{border-top:1px solid #5a3a33;display:flex;justify-content:space-between;align-items:center;height:62px;font-size:13px}
.social{display:flex;gap:14px;margin-right:46px}
.social i{width:14px;height:14px;border-radius:50%;background:var(--white);display:block}
</style>
</head>
<body>

<header class="site-header">
  <div class="wrap">
    <div class="brand"><span class="brand-dot"></span>Tiny-ThreadDays</div>
    <nav class="main-nav">
      <span class="active">HOME</span><span>ABOUT</span><span>CAMPS</span><span>HOW IT WORKS</span><span>FAQ</span><span>CONTACT</span>
    </nav>
    <div class="header-tools">
      <span>ENG ⌄</span>
      <svg width="16" height="16" viewBox="0 0 16 16" fill="none" stroke="#1f2328" stroke-width="1.6"><circle cx="7" cy="7" r="5.2"/><path d="M11 11l4 4"/></svg>
    </div>
  </div>
</header>

<section class="hero" role="img" aria-label="Children sewing at machines in a bright fabric-lined studio">
  <h1>Discover the joy of sewing<span>Holiday camps for kids<br>in Switzerland</span></h1>
  <p>A week of creativity, friendship, and fun — where young talents<br>learn to sew and create their own fashion pieces!</p>
  <span class="btn">Learn more</span>
</section>

<div class="wrap">
  <section class="mentors" role="img" aria-label="Kids working at sewing machines with colourful fabrics">
    <h2>Experienced, passionate,<br>and creative mentors</h2>
    <p>Greta and Lina have over 10 years of experience teaching children sewing, tailoring, and design — always with fun, structure, and creativity.</p>
    <span class="btn">Learn more</span>
  </section>

  <section class="how">
    <div class="section-head"><h2>How the Camp Works</h2></div>
    <div class="steps">
      <div class="step"><div class="ph" role="img" aria-label="Sewing patterns, buttons and thread on a table" style="background:linear-gradient(135deg,#e9e3d8,#3aa8a4 60%,#f0c24a)"></div><h3>Project Selection</h3></div>
      <div class="step"><div class="ph" role="img" aria-label="Stack of soft coloured fabrics" style="background:linear-gradient(160deg,#b58fb9,#d6747a 40%,#e7b88b 70%,#7aa3c7)"></div><h3>Fabric Selection</h3></div>
      <div class="step"><div class="ph" role="img" aria-label="Mentor showing a child how to use a sewing machine" style="background:linear-gradient(135deg,#3b2a22,#a36c47 60%,#e7c9a3)"></div><h3>Learn the Machine</h3></div>
      <div class="step"><div class="ph" role="img" aria-label="Children showing their finished sewn vests" style="background:linear-gradient(180deg,#dfe3e6,#e38a49 60%,#5b7fb0)"></div><h3>Sewing &amp; Refining</h3></div>
    </div>
  </section>
</div>

<section class="features">
  <div class="wrap">
    <div class="section-head"><h2>A Week Full of Creativity and Confidence</h2></div>
    <div class="feature-list">
      <div class="feature" style="width:208px"><strong>Small Groups (max. 8)</strong>Personalized attention and mentoring.</div>
      <div class="feature" style="width:231px"><strong>Multilingual (DE / EN / IT)</strong>Friendly, inclusive<br>guidance.</div>
      <div class="feature" style="width:189px"><strong>Premium Fabrics</strong>High-quality Stichwerk<br>machines.</div>
      <div class="feature" style="width:216px"><strong>Safe, Central Locations</strong>Zurich and nearby, easily<br>accessible.</div>
      <div class="feature" style="width:134px"><strong>Pick-Up Service</strong>Convenient service from Zurich Main Station.</div>
    </div>
  </div>
</section>

<div class="wrap">
  <section class="camps">
    <div class="section-head"><h2>Upcoming Camps</h2></div>
    <div class="camp-list">
      <div class="camp"><div class="ph" role="img" aria-label="Spring sewing class with dresses on a rail" style="background:linear-gradient(160deg,#e8e4de,#e86b8a 55%,#7ac0c4)"></div><h3>Spring Camps</h3><p>Fresh creativity blooms with spring-inspired projects.</p></div>
      <div class="camp"><div class="ph" role="img" aria-label="Children outdoors in a summer meadow with their creations" style="background:linear-gradient(180deg,#cfe0e6,#9bb37a 45%,#5f9a3c)"></div><h3>Summer Camps</h3><p>Sunny days, bright fabrics, and full-week creative fun.</p></div>
      <div class="camp"><div class="ph" role="img" aria-label="Autumn sewing workshop at a table" style="background:linear-gradient(160deg,#dfe1e3,#b9a79a 50%,#d3533d)"></div><h3>Autumn Camps</h3><p>Cozy sewing projects for<br>cooler days.</p></div>
    </div>
    <div class="center"><span class="btn">View all camps</span></div>
  </section>

  <section class="faq">
    <div class="section-head"><h2>Frequently Asked Questions</h2></div>
    <div class="faq-list">
      <div class="faq-item"><h3><svg width="14" height="16" viewBox="0 0 14 16" fill="none" stroke="#e0684f" stroke-width="1.2"><path d="M1 1h8l4 4v10H1z"/><path d="M4 8h6M4 11h6"/></svg>Does my child need prior experience?</h3><p>No — we welcome beginners and advanced young creators alike.</p><svg class="toggle" width="20" height="20" viewBox="0 0 20 20" stroke="#245f68" stroke-width="1.6"><path d="M2 6h16"/></svg></div>
      <div class="faq-item"><h3><svg width="14" height="16" viewBox="0 0 14 16" fill="none" stroke="#e0684f" stroke-width="1.2"><path d="M1 1h8l4 4v10H1z"/><path d="M4 8h6M4 11h6"/></svg>How many children per group?</h3><svg class="toggle" width="20" height="20" viewBox="0 0 20 20" stroke="#245f68" stroke-width="1.6"><path d="M2 10h16M10 2v16"/></svg></div>
      <div class="faq-item"><h3><svg width="14" height="16" viewBox="0 0 14 16" fill="none" stroke="#e0684f" stroke-width="1.2"><path d="M1 1h8l4 4v10H1z"/><path d="M4 8h6M4 11h6"/></svg>Do you provide fabrics and materials?</h3><svg class="toggle" width="20" height="20" viewBox="0 0 20 20" stroke="#245f68" stroke-width="1.6"><path d="M2 10h16M10 2v16"/></svg></div>
      <div class="faq-item"><h3><svg width="14" height="16" viewBox="0 0 14 16" fill="none" stroke="#e0684f" stroke-width="1.2"><path d="M1 1h8l4 4v10H1z"/><path d="M4 8h6M4 11h6"/></svg>Where are the camps located?</h3><svg class="toggle" width="20" height="20" viewBox="0 0 20 20" stroke="#245f68" stroke-width="1.6"><path d="M2 10h16M10 2v16"/></svg></div>
      <div class="faq-item"><h3><svg width="14" height="16" viewBox="0 0 14 16" fill="none" stroke="#e0684f" stroke-width="1.2"><path d="M1 1h8l4 4v10H1z"/><path d="M4 8h6M4 11h6"/></svg>What happens at the fashion show?</h3><svg class="toggle" width="20" height="20" viewBox="0 0 20 20" stroke="#245f68" stroke-width="1.6"><path d="M2 10h16M10 2v16"/></svg></div>
    </div>
    <div class="center"><span class="btn">View all</span></div>
  </section>
</div>

<section class="loop">
  <div class="wrap">
    <div>
      <h2>Stay in the Loop!</h2>
      <p>Join our community of creative parents and receive updates about new<br>camps, fashion shows, and early bird offers.</p>
    </div>
    <span class="btn">Subscribe now</span>
  </div>
</section>

<footer class="site-footer">
  <div class="wrap">
    <div class="footer-cols">
      <div class="footer-brand">
        <div class="brand" style="color:var(--coral)"><span class="brand-dot"></span>Tiny-ThreadDays</div>
        <small>SEWING | NÄHEN | CUCITO</small>
      </div>
      <div class="footer-col"><h4>QUICK LINKS</h4><ul><li>Home</li><li>About</li><li>Camps</li><li>How it works</li><li>FAQ</li><li>Contact</li></ul></div>
      <div class="footer-col" style="width:168px"><h4>LINKS</h4><ul><li>Copyright</li><li>Legal</li><li>Privacy</li><li>Accessibility</li><li>Sitemap</li></ul></div>
      <div class="footer-news"><h4 style="font-size:16px;font-weight:600;margin-bottom:12px">NEWSLETTER</h4><p>Subscribe to our newsletter<br>and receive special offers</p><div class="signup"><span>Your Email</span><b>SUBSCRIBE</b></div></div>
    </div>
    <div class="footer-bottom">
      <span>©2025. All rights reserved.</span>
      <div class="social"><i></i><i></i></div>
    </div>
  </div>
</footer>

</body>
</html>
```